New Business Cards for Tormin Group

We need a new Business Card to compliment our new logo. We are a vibrant design, manufacture and install business providing recreation areas, public parks and Municipal spaces. We want business cards that are classy, modern and clean.

We have recently changed our logo, and are celebrating our 40th anniversary. We want business cards with a new modern design to reflect our status.

Target Market(s)

Customers

Contact Information for Business Card

We need all the details of our 3 offices as per the business card attached. Please disregard the old logo on the business card, the other three files show our new logo.

Requirements
Must have
• All info as per attached business card but with new logo.
Nice to have

```html
<!DOCTYPE html>
<html lang="en">
<head>
<meta charset="utf-8">
<title>Tormin Group Business Cards</title>
<link rel="stylesheet" href="https://fonts.googleapis.com/css2?family=Roboto+Condensed:wght@400;700&family=Open+Sans:wght@400;600&display=swap">
<style>
:root{
  --red:#e62b36;
  --red-light:#f04a54;
  --ink:#3a3a3c;
  --grey:#58595b;
  --paper:#ffffff;
  --stage:#e9e9ea;
}
*{box-sizing:border-box;margin:0;padding:0}
html,body{width:1200px;height:896px;overflow:hidden}
body{background:var(--stage);font-family:"Roboto Condensed",Arial,sans-serif;color:var(--ink);position:relative}
.card{position:absolute;width:540px;height:310px;border-radius:18px;overflow:hidden;box-shadow:0 10px 28px rgba(0,0,0,.18)}
.card--offices{left:40px;top:293px;background:var(--paper)}
.card--personal{left:620px;top:293px;background:linear-gradient(135deg,var(--red-light),var(--red))}

.brand{position:absolute;display:flex;align-items:center;gap:10px}
.brand__dot{width:44px;height:44px;border-radius:50%;background:var(--red);flex:none}
.brand__name{font-family:"Roboto Condensed",Arial,sans-serif;font-weight:700;font-size:30px;color:var(--ink);letter-spacing:.5px;text-transform:uppercase;line-height:1}
.card--offices .brand{left:30px;top:30px}

.offices{position:absolute;left:30px;right:20px;top:130px;display:grid;grid-template-columns:repeat(3,1fr);gap:14px}
.office__title{color:var(--red);font-size:20px;font-weight:400;margin-bottom:6px}
.office__line{font-size:13px;line-height:1.45;color:var(--ink)}
.office__gap{height:10px}
.office__label{color:var(--red)}

.card--personal .arc{position:absolute;right:-60px;top:-120px;width:400px;height:400px}
.card--personal .brand{right:48px;top:72px}
.card--personal .brand__name{font-size:28px}

.person{position:absolute;left:30px;bottom:26px;color:#fff}
.person__name{font-family:"Open Sans",Arial,sans-serif;font-weight:600;font-size:20px;letter-spacing:.5px;text-transform:uppercase}
.person__role{font-family:"Open Sans",Arial,sans-serif;font-size:13px;margin-top:2px}
.person__rule{width:14px;height:1px;background:#fff;margin:14px 0 10px}
.contact{display:flex;align-items:center;gap:8px;font-family:"Open Sans",Arial,sans-serif;font-size:13px;line-height:1.7}
.contact svg{width:11px;height:11px;flex:none}
</style>
</head>
<body>

<section class="card card--offices">
  <div class="brand">
    <span class="brand__dot"></span>
    <span class="brand__name">Tormin Group</span>
  </div>
  <div class="offices">
    <div class="office">
      <h2 class="office__title">Head Office</h2>
      <p class="office__line">P.O. Box:</p>
      <p class="office__line">41820 Abu Dhabi, U.A.E.</p>
      <div class="office__gap"></div>
      <p class="office__line"><span class="office__label">P :</span> +971 (0)2 5550142</p>
      <p class="office__line"><span class="office__label">F :</span> +971 (0)2 5550143</p>
      <p class="office__line"><span class="office__label">E :</span> sales@tormingroup.com</p>
    </div>
    <div class="office">
      <h2 class="office__title">Dubai Office</h2>
      <p class="office__line">P.O. Box:</p>
      <p class="office__line">275410 Dubai, U.A.E.</p>
      <div class="office__gap"></div>
      <p class="office__line"><span class="office__label">P :</span> +971 (0)4 5550278</p>
      <p class="office__line"><span class="office__label">F :</span> +971 (0)4 5550279</p>
      <p class="office__line"><span class="office__label">E :</span> sales@tormingroup.com</p>
    </div>
    <div class="office">
      <h2 class="office__title">Qatar Office</h2>
      <p class="office__line">P.O. Box:</p>
      <p class="office__line">30862 Doha, Qatar</p>
      <div class="office__gap"></div>
      <p class="office__line"><span class="office__label">P :</span> +974 55503310</p>
      <p class="office__line"><span class="office__label">F :</span> +974 55503311</p>
      <p class="office__line"><span class="office__label">E :</span> sales@tormingroup.com</p>
    </div>
  </div>
</section>

<section class="card card--personal">
  <svg class="arc" viewBox="0 0 400 400" aria-hidden="true">
    <circle cx="200" cy="200" r="190" fill="#58595b"/>
    <circle cx="206" cy="192" r="186" fill="#ffffff"/>
  </svg>
  <div class="brand">
    <span class="brand__dot"></span>
    <span class="brand__name">Tormin Group</span>
  </div>
  <div class="person">
    <h1 class="person__name">Sam Derwent</h1>
    <p class="person__role">Managing Partner</p>
    <div class="person__rule"></div>
    <p class="contact">
      <svg viewBox="0 0 12 12"><path d="M2.5 1 L4.5 3.2 3.6 4.4 C4.3 5.9 6.1 7.7 7.6 8.4 L8.8 7.5 11 9.5 9.8 11 C5.5 10.7 1.3 6.5 1 2.2 Z" fill="#fff"/></svg>
      +971 (0)50 555 0187
    </p>
    <p class="contact">
      <svg viewBox="0 0 12 12"><rect x="1" y="2.5" width="10" height="7" fill="none" stroke="#fff" stroke-width="1.2"/><path d="M1 2.5 L6 6.5 11 2.5" fill="none" stroke="#fff" stroke-width="1.2"/></svg>
      sam@tormingroup.com
    </p>
    <p class="contact">
      <svg viewBox="0 0 12 12"><circle cx="6" cy="6" r="5" fill="none" stroke="#fff" stroke-width="1.2"/><path d="M1 6 H11 M6 1 C3.5 4 3.5 8 6 11 M6 1 C8.5 4 8.5 8 6 11" fill="none" stroke="#fff" stroke-width="1"/></svg>
      www.tormingroup.com
    </p>
  </div>
</section>

</body>
</html>
```